Professional, Attractive, Simple Website Needed!!

We completed the design for our logo.

We need a website built out around this.

Here are a couple samples of how we want ours formatted.

http://brimvoltco.com

http://www.ravelbeam.com/lp/free-quote?LeadSource=Search%20Engine&ProgramName=searchads&experience=qual&language=en&type=brd&gclid=Xk7PLmqwTRZBNVuEYcaHdFgWsLoPeRtQnMxVbCzJaKiOuYtReWqAsDfGhJkLzXcVbNmQwErTyUiOpAsDfGhJkLzX_wcB

http://quorel.co
Updates

Project Deadline Extended
Reason: Extending this deadline due to our delay in providing designers with content for each page. This is coming in next 24 hours.

Project Deadline Extended
Reason: Due to scheduling conflicts and extended travel delays related to Puerto Rico, the deadline has been extended. Your patience is greatly appreciated.

Project Deadline Extended
Reason: Travel and scheduling conflicts have made it impossible to give this project the thorough review it deserves, therefore I am extending the deadline. Thank you for your patience!

Target Market(s)

Home Owners who earn 60k + household annually

Industry/Entity Type

It Professional

Coding

Coded - Design and coding required

Number of Pages Required

5+ page

Font styles to use
Serif

Colors
34a7d8
9bcb3c

Requirements
Must have
• Simple
• Lead form Entry (Ability for visitor to enter Name, number and address for a quote)
• Sleek Design
• Professional
• Testimonials
• Use color Scheme of Design Logo Attached
Nice to have
• Video when site starts
• Like this
• https://www.vidplexa.com/watch?v=Qm8rTbLw3Np&feature=vidplexa.be
Should not have
• Should not include Commercial solar
• Should not include wind power

```html
<!DOCTYPE html>
<html lang="en">
<head>
<meta charset="utf-8">
<title>Solvane Energy</title>
<link href="https://fonts.googleapis.com/css2?family=Mulish:ital,wght@0,400;0,600;0,700;1,400&display=swap" rel="stylesheet">
<style>
:root{
  --blue:#34a7d8;
  --band:#3aa9dc;
  --green:#9bcb3c;
  --quote-green:#a8d24b;
  --ink:#3a3a3a;
  --muted:#8a8a8a;
  --white:#ffffff;
  --line:#e2e2e2;
}
*{box-sizing:border-box;margin:0;padding:0}
html,body{width:798px;height:1200px;overflow:hidden;background:var(--white)}
body{position:relative;font-family:'Mulish',sans-serif;color:var(--ink)}
.abs{position:absolute}
.hero{left:0;top:0;width:798px;height:436px;
  background:linear-gradient(160deg,#1f86e3 0%,#3c9ff0 30%,#2f5fa8 52%,#c9562a 74%,#7a8a4a 100%)}
.brand{left:78px;top:12px;display:flex;align-items:center;gap:8px;color:var(--white)}
.brand-mark{width:50px;height:50px;border:3px solid var(--white);border-radius:50%}
.brand-name{font-size:19px;font-weight:600;letter-spacing:.5px}
.nav{top:30px;left:0;height:16px;font-size:10.5px;font-weight:600;color:var(--white)}
.nav span{position:absolute;white-space:nowrap}
.nav-home{left:335px;top:14px;width:49px;height:49px;border:2px solid var(--white);border-radius:50%;
  display:flex;align-items:center;justify-content:center;color:var(--white);font-size:10.5px;font-weight:600}
.play{left:360px;top:176px;width:77px;height:77px;border-radius:50%;background:var(--white);
  box-shadow:0 0 0 4px rgba(60,60,60,.35)}
.quote-box{left:509px;top:116px;width:215px;height:197px;background:var(--quote-green);padding:0 17px}
.quote-box h2{font-size:14px;font-weight:600;color:var(--white);text-align:center;margin-top:22px;padding-bottom:6px;border-bottom:1.5px solid var(--white);letter-spacing:.3px}
.field{width:179px;height:22px;background:var(--white);font-size:8px;color:#666;padding:0 8px;display:flex;align-items:center;position:absolute;left:19px}
.submit{position:absolute;left:19px;top:146px;width:179px;height:26px;background:var(--blue);color:var(--white);font-size:11px;font-weight:600;display:flex;align-items:center;justify-content:center}
.card{top:415px;height:143px;background:var(--white);border:1px solid var(--line);text-align:center}
.card h3{font-size:16px;font-weight:400;margin-top:50px;color:var(--ink)}
.card p{font-size:8px;line-height:12.7px;color:var(--muted);margin-top:9px}
.card .btn{position:absolute;left:50%;transform:translateX(-50%);top:127px;width:97px;height:26px;background:var(--blue);color:var(--white);font-size:9.5px;font-weight:600;display:flex;align-items:center;justify-content:center}
.feature-photo{width:96px;height:96px;border-radius:50%;border:2px solid var(--white);top:358px}
.intro{left:0;top:620px;width:798px;text-align:center}
.intro h2{font-size:19px;font-weight:400;letter-spacing:.5px;color:var(--ink)}
.intro p{font-size:10px;line-height:20.7px;color:var(--muted);margin-top:16px}
.outline-btn{left:358px;top:760px;width:96px;height:25px;border:2px solid var(--green);color:var(--green);font-size:9px;font-weight:700;display:flex;align-items:center;justify-content:center}
.testimonials{left:0;top:838px;width:798px;height:268px;background:var(--band)}
.scenery{left:0;top:930px;width:798px;height:176px;background:linear-gradient(180deg,rgba(255,255,255,0) 0%,rgba(30,140,200,.35) 100%)}
.testimonials-title{left:0;top:870px;width:798px;text-align:center;color:var(--white);font-size:18px;font-weight:400;letter-spacing:.4px}
.t-card{top:909px;width:264px;height:109px;background:var(--white);text-align:center;padding-top:20px}
.t-card p{font-size:9.5px;font-style:italic;line-height:17.6px;color:var(--muted)}
.badge{width:30px;height:30px;border-radius:50%;background:var(--green);top:895px;color:var(--white);font-size:13px;font-weight:700;font-style:italic;display:flex;align-items:center;justify-content:center}
.avatar{width:44px;height:44px;border-radius:50%;background:#c89a78;border:2px solid var(--white)}
.author{width:200px;text-align:center;color:var(--white)}
.author b{display:block;font-size:10.5px;font-weight:600}
.author span{display:block;font-size:8.5px;margin-top:3px}
.foot-nav span{position:absolute;top:1128px;font-size:10.5px;font-weight:600;color:#555}
.copyright{left:82px;top:1153px;font-size:8.5px;color:#999}
.social{top:1127px;width:25px;height:25px;border:1.5px solid var(--green);border-radius:50%}
</style>
</head>
<body>
<div class="abs hero" role="img" aria-label="Photo of a house roof covered with solar panels under a blue sky"></div>

<div class="abs brand"><div class="brand-mark"></div><div class="brand-name">SOLVANE ENERGY</div></div>
<div class="abs nav-home">HOME</div>
<div class="abs nav" style="width:798px">
  <span style="left:402px">ABOUT US</span>
  <span style="left:484px">WHY</span>
  <span style="left:537px">SERVICES</span>
  <span style="left:614px">BLOG</span>
  <span style="left:670px">CONTACT</span>
</div>

<div class="abs play">
  <svg width="77" height="77" viewBox="0 0 77 77"><polygon points="31,24 55,38.5 31,53" fill="#3a3a3a"/></svg>
</div>

<div class="abs quote-box">
  <h2>REQUEST A QUOTE</h2>
  <div class="field" style="top:57px">Name</div>
  <div class="field" style="top:84px">Phone number</div>
  <div class="field" style="top:114px">Address</div>
  <div class="submit">SUBMIT</div>
</div>

<div class="abs card" style="left:78px;width:214px">
  <h3>Why We Are</h3>
  <p>Aortor at ipsum cligula augue bibendum<br>accumsan vestibulum ut commodo uam<br>Curabitur vel dolor ultrices</p>
  <div class="btn">READ MORE</div>
</div>
<div class="abs card" style="left:294px;width:212px">
  <h3>Low Maintenance</h3>
  <p>Aortor at ipsum cligula augue bibendum<br>accumsan vestibulum ut commodo uam<br>Curabitur vel dolor ultrices</p>
  <div class="btn">READ MORE</div>
</div>
<div class="abs card" style="left:508px;width:214px">
  <h3>Environment Friendly</h3>
  <p>Aortor at ipsum cligula augue bibendum<br>accumsan vestibulum ut commodo uam<br>Curabitur vel dolor ultrices</p>
  <div class="btn">READ MORE</div>
</div>
<div class="abs feature-photo" style="left:142px;background:linear-gradient(180deg,#4a8fd8,#2e4f8a)" role="img" aria-label="Solar panel field"></div>
<div class="abs feature-photo" style="left:350px;background:linear-gradient(180deg,#3e7fc8,#2a4470)" role="img" aria-label="Installer fitting panels on a roof"></div>
<div class="abs feature-photo" style="left:566px;background:radial-gradient(circle,#f2d27a,#8a7a2a)" role="img" aria-label="Glowing light bulb in nature"></div>

<div class="abs intro">
  <h2>SOLVANE ENERGY</h2>
  <p>Praesent elementum elit at tellus nec ultricies sit amet porttitor mattis enim In massa libero interdum nec interdum vel<br>blandit sed nulla In ullamcorper est eget tempor cursus neque mi consectetuer mi a ultricies<br>massa est sed nisl Class aptent taciti sociosqu ad litora torquent per conubia nostra per inceptos hymenaipsum dui<br>aliquet felis at cursus magna nisl nec elit Praesent elementum elit at tellus nec</p>
</div>
<div class="abs outline-btn">READ MORE</div>

<div class="abs testimonials"></div>
<div class="abs scenery" role="img" aria-label="Faint landscape silhouette with trees and panels"></div>
<div class="abs testimonials-title">TESTIMONIALS</div>

<div class="abs t-card" style="left:124px">
  <p>Morbi ornare gravida elit Integer congue augue et<br>malesuada iaculis ipsum dui aliquet felis at cursus<br>magna nisl nec elit Praesent elementum</p>
</div>
<div class="abs t-card" style="left:408px">
  <p>Morbi ornare gravida elit Integer congue augue et<br>malesuada iaculis ipsum dui aliquet felis at cursus<br>magna nisl nec elit Praesent elementum</p>
</div>
<div class="abs badge" style="left:241px">//</div>
<div class="abs badge" style="left:525px">//</div>
<div class="abs avatar" style="left:234px;top:990px" role="img" aria-label="Customer portrait"></div>
<div class="abs avatar" style="left:522px;top:991px;background:#b88a74" role="img" aria-label="Customer portrait"></div>
<div class="abs author" style="left:159px;top:1037px"><b>By Author Name,</b><span>City Location</span></div>
<div class="abs author" style="left:440px;top:1040px"><b>By Author Name,</b><span>City Location</span></div>

<div class="foot-nav">
  <span style="left:82px">HOME</span>
  <span style="left:140px">ABOUT US</span>
  <span style="left:222px">WHY</span>
  <span style="left:274px">SERVICES</span>
  <span style="left:352px">BLOG</span>
  <span style="left:408px">CONTACT</span>
</div>
<div class="abs copyright">© 2017 Company Name &nbsp;All right reserved</div>
<div class="abs social" style="left:605px"></div>
<div class="abs social" style="left:635px"></div>
<div class="abs social" style="left:665px"></div>
<div class="abs social" style="left:695px"></div>
</body>
</html>
```